English and Spanish Language School Needs a Business Card

Need a business card design a startup company called Maribel Language School. The company will offer English and Spanish conversational level courses designed to make the learner feel comfortable with grammar and vocabulary. We would like to see a logo with some colour that should communicate learning, growth.

Target Market(s)

Consumers and businesses

Industry/Entity Type

Education

Contact Information for Business Card

TBD

Font styles to use
Serif

Requirements
Must have
• Include the following
• Logo
• Name
• Title
• Cellphone Number
• Office Phone number
• Email address
• Office Address

```html
<!DOCTYPE html>
<html lang="en">
<head>
<meta charset="utf-8">
<title>Maribel Language School – Business Card</title>
<link href="https://fonts.googleapis.com/css2?family=Tinos:wght@400;700&display=swap" rel="stylesheet">
<style>
  :root {
    --page-bg: #e9e3da;
    --card-white: #f6f4f1;
    --brand-red: #a51d2a;
    --brand-red-deep: #8e1622;
    --brand-teal: #137a7c;
    --teal-band: #1f7f80;
    --ink-cream: #f4ddd2;
    --ink-soft: #e9c4b9;
    --divider: rgba(244, 221, 210, 0.7);
  }
  * { margin: 0; padding: 0; box-sizing: border-box; }
  html, body { width: 1200px; height: 970px; overflow: hidden; }
  body {
    background: var(--page-bg);
    font-family: "Tinos", "Times New Roman", serif;
  }
  .card {
    position: absolute;
    left: 100px;
    top: 200px;
    width: 1000px;
    height: 567px;
    border-radius: 26px;
    overflow: hidden;
    box-shadow: 0 18px 40px rgba(60, 40, 30, 0.25);
  }
  .card-shapes { position: absolute; inset: 0; }
  .logo {
    position: absolute;
    left: 0; right: 0;
    top: 70px;
    text-align: center;
    color: var(--brand-red);
    font-weight: 700;
  }
  .logo-name { font-size: 112px; line-height: 1; letter-spacing: -1px; display: block; }
  .logo-tagline { font-size: 32px; line-height: 1.1; display: block; margin-top: 2px; }
  .person {
    position: absolute;
    right: 525px;
    top: 382px;
    text-align: right;
    color: var(--ink-cream);
  }
  .person-name { font-size: 37px; font-weight: 700; letter-spacing: 1px; line-height: 1.05; }
  .person-title { font-size: 26px; color: var(--ink-soft); line-height: 1.1; }
  .divider {
    position: absolute;
    left: 500px; top: 378px;
    width: 1px; height: 102px;
    background: var(--divider);
  }
  .contacts {
    position: absolute;
    left: 523px; top: 380px;
    list-style: none;
    color: var(--ink-soft);
    font-size: 28px;
    line-height: 32px;
  }
  .contacts li { display: flex; align-items: center; gap: 10px; }
  .contacts svg { width: 24px; height: 24px; fill: var(--ink-soft); flex: none; }
  .address {
    position: absolute;
    left: 228px; top: 527px;
    font-size: 26px;
    color: var(--ink-soft);
    white-space: nowrap;
  }
</style>
</head>
<body>
  <section class="card" aria-label="Business card">
    <svg class="card-shapes" viewBox="0 0 1000 567" width="1000" height="567" aria-hidden="true">
      <defs>
        <linearGradient id="red-field" x1="0" y1="0" x2="0" y2="1">
          <stop offset="0" stop-color="#b42c36"/>
          <stop offset="1" stop-color="#8f1a25"/>
        </linearGradient>
      </defs>
      <rect width="1000" height="567" fill="var(--card-white)"/>
      <path d="M0 192 Q500 470 1000 182 L1000 514 L0 514 Z" fill="url(#red-field)"/>
      <path d="M0 190 Q500 440 1000 178" fill="none" stroke="#ffffff" stroke-width="10"/>
      <path d="M0 196 Q500 430 1000 184 Q500 410 0 196 Z" fill="var(--brand-teal)"/>
      <rect y="514" width="1000" height="53" fill="var(--teal-band)"/>
    </svg>

    <div class="logo">
      <span class="logo-name">Maribel</span>
      <span class="logo-tagline">Language School</span>
    </div>

    <div class="person">
      <p class="person-name">DANIEL REYES</p>
      <p class="person-title">Manager</p>
    </div>

    <div class="divider"></div>

    <ul class="contacts">
      <li>
        <svg viewBox="0 0 24 24"><path d="M7 2h10a1 1 0 0 1 1 1v18a1 1 0 0 1-1 1H7a1 1 0 0 1-1-1V3a1 1 0 0 1 1-1zm1 3v10h8V5H8zm4 12a1.3 1.3 0 1 0 0 2.6A1.3 1.3 0 0 0 12 17z"/></svg>
        <span>555 014 2290</span>
      </li>
      <li>
        <svg viewBox="0 0 24 24"><path d="M3 9c0-3 4-5 9-5s9 2 9 5v1h-5V8H8v2H3V9zm4 3h10l3 8H4l3-8zm5 2a2.5 2.5 0 1 0 0 5 2.5 2.5 0 0 0 0-5z"/></svg>
        <span>555 014 2291</span>
      </li>
      <li>
        <svg viewBox="0 0 24 24"><path d="M2 5h20v14H2V5zm2 2v.5l8 6 8-6V7H4zm0 3v7h16v-7l-8 6-8-6z"/></svg>
        <span>hello@maribelschool.com</span>
      </li>
    </ul>

    <p class="address">18 Alder Road, Suite 2, Fairview, Texas 7710</p>
  </section>
</body>
</html>
```